Kestrelway Financial Plans

I am looking for a complete resdesign of my small financial presentation. This is a Word Doc/PDF that I print off when meeting with people in private. I often present my "two pager" that I have been using for years and years. It tells them the basics of what I do, how I help people and foundational financial principles.

I have recently gone out on my own in business and have completely rebranded. This presentation is my most used tool, so it is the first of many things I would like to redo. I am hoping it will somehow coordinate with the colors of my business, not necessarily the EXACT same 3 colors everywhere, but have the design colors compliment.

I've uploaded all my logo designs, as well as the current "two-pager". I am not against it going to 3 pages if needed. As it will still land on 2 pages with duplex printing.

It has always been VERY simple. I am wanting it built into a more professional and design specific format, to show off my branding, without being over cluttered.

I am completely open to ANY graphics changes. Obviously some are very novice, the house on the last page has always been overly simplified.

```html
<!DOCTYPE html>
<html lang="en">
<head>
<meta charset="utf-8">
<title>Kestrelway Financial Plans – Two Pager</title>
<link href="https://fonts.googleapis.com/css2?family=Montserrat:wght@300;400;500;600;700;800&display=swap" rel="stylesheet">
<style>
:root{
  --navy:#0e2235;
  --navy-2:#16324a;
  --green:#16b14a;
  --green-dark:#0b6b34;
  --mint:#b9f3cb;
  --paper:#ffffff;
  --panel:#f1f1f1;
  --stage:#e8e8e8;
  --stone:#b7bbc0;
  --stone-2:#cdd0d3;
  --slate:#8d9298;
  --red:#e3191f;
}
*{box-sizing:border-box;margin:0;padding:0}
html,body{width:1200px;height:2401px;overflow:hidden;background:var(--stage);font-family:'Montserrat',sans-serif;color:var(--navy)}
.sheet{position:absolute;left:0;top:0;width:1288px;height:2576px;transform:scale(.931677);transform-origin:0 0}
.page{position:absolute;left:235px;width:818px;background:var(--paper);box-shadow:0 1px 4px rgba(0,0,0,.12);overflow:hidden}
.page-one{top:73px;height:1183px}
.page-two{top:1322px;height:1181px}
.abs{position:absolute}

.brand{position:absolute;left:55px;top:28px;width:155px;text-align:center;color:var(--navy);font-weight:600}
.brand-name{font-size:22px;letter-spacing:.5px;line-height:24px}
.brand-sub{display:flex;align-items:center;gap:6px;font-size:8.5px;letter-spacing:1.6px;margin-top:2px}
.brand-sub::before,.brand-sub::after{content:"";flex:1;height:1.5px;background:var(--navy)}

.pattern{position:absolute;left:645px;top:0;width:173px;height:130px;background:linear-gradient(225deg,rgba(22,177,74,.28),rgba(183,187,192,.18) 55%,rgba(255,255,255,0) 85%)}

.heading{position:absolute;font-weight:800;font-size:25px;line-height:27px;letter-spacing:.2px}
.heading .accent{color:var(--green);display:block}

/* challenge cards */
.fact-card{position:absolute;left:54px;width:264px;border-radius:14px;overflow:hidden;color:#fff;padding:14px 14px 0 20px}
.fact-photo{position:absolute;inset:0;background:linear-gradient(135deg,#3b4f5e 0%,#24394b 55%,#142a3c 100%)}
.fact-card > *:not(.fact-photo){position:relative}
.fact-title{display:flex;align-items:center;gap:9px;font-size:22px;font-weight:700;height:50px;margin-bottom:4px}
.fact-card p{font-size:13px;line-height:15.6px;font-weight:300;letter-spacing:-.15px}
.fact-card b{font-weight:700}
.source{display:inline-block;background:var(--green);border-radius:10px;font-size:10.5px;font-weight:600;padding:3px 11px;margin:6px 0 12px}

.icon-ring{width:46px;height:46px;border-radius:50%;background:#fff;border:1.5px dashed var(--green);display:flex;align-items:center;justify-content:center;flex:none}
.icon-ring svg{width:24px;height:24px;stroke:var(--green);fill:none;stroke-width:1.8;stroke-linecap:round;stroke-linejoin:round}
.icon-ring.sm{width:40px;height:40px}
.icon-ring.sm svg{width:21px;height:21px}

/* step grid */
.step{position:absolute;width:135px;height:174px;background:var(--panel);border-radius:12px}
.step-head{height:65px;background:var(--navy);border-radius:12px 12px 0 0;color:#fff;font-size:11.5px;font-weight:700;text-align:center;line-height:13px;padding-top:30px}
.step .icon-ring{position:absolute;left:47px;top:-18px}
.step-line{position:absolute;left:0;right:0;text-align:center;font-size:11.5px;font-weight:700;line-height:13px}
.step-line.small{font-size:10px;line-height:12px}
.tri{position:absolute;width:0;height:0;border-left:9px solid transparent;border-right:9px solid transparent;border-top:12px solid var(--green)}
.tri.grey{border-left-width:10px;border-right-width:10px;border-top:13px solid #5a6068}
.tri-right{position:absolute;width:0;height:0;border-top:6px solid transparent;border-bottom:6px solid transparent;border-left:10px solid var(--green)}
.tiny{position:absolute;font-size:10.5px;line-height:12px;font-weight:500}

/* services */
.service{position:absolute;top:864px;width:103px;height:87px;background:var(--navy-2);border-radius:8px;color:#fff;text-align:center;font-size:10.5px;font-weight:700;line-height:13px;padding-top:50px}
.service .icon-ring{position:absolute;left:33px;top:10px;width:36px;height:36px;border-style:dashed;border-color:#fff;background:transparent}
.service .icon-ring svg{stroke:#fff;width:19px;height:19px}

.partner{position:absolute;width:103px;height:37px;background:var(--panel);border-radius:5px;display:flex;align-items:center;justify-content:center;font-size:11px;font-weight:600;color:var(--navy-2);text-align:center;line-height:12px}

.footer{position:absolute;left:100px;right:0;height:38px;background:linear-gradient(90deg,var(--navy) 0%,var(--navy) 45%,var(--green-dark) 100%);color:#fff;font-size:12.5px;font-weight:500;display:flex;align-items:center;justify-content:flex-end;padding-right:24px;gap:9px}
.footer .num{width:20px;height:20px;border:1.5px solid #fff;border-radius:50%;display:flex;align-items:center;justify-content:center;font-size:11px}

/* rule of 72 */
.upper{position:absolute;left:0;top:0;width:818px;height:493px;background:var(--panel)}
.rate-block{position:absolute;top:156px}
.rate-head{display:flex;height:42px;font-size:19px;font-weight:700;color:#fff}
.rate-head span{display:flex;align-items:center;justify-content:center}
.rate-head .age{background:var(--navy)}
.rate-head .pct{background:var(--green);flex:1}
.rate-row{display:flex;height:30px;border-bottom:1.5px solid #6e7378;font-size:15px}
.rate-row span{display:flex;align-items:center;justify-content:center}
.rate-row .a{font-weight:400}
.rate-row span:last-child{flex:1}
.first .rate-row .a{font-weight:700}
.doubles{position:absolute;top:404px;display:flex;align-items:center;gap:10px}
.doubles svg{width:50px;height:40px}
.doubles-text{font-weight:800;line-height:15px}
.doubles-text .lead{font-size:14px;color:var(--navy);display:block}
.doubles-text .every{font-size:19px;color:var(--green);display:block;line-height:17px}

/* structure */
.no-sign{position:absolute;left:596px;top:530px;display:flex;align-items:center;gap:8px;font-size:19px;font-weight:800;color:var(--navy);white-space:nowrap}
.no-sign .ring{width:40px;height:40px;border:5px solid var(--red);border-radius:50%;flex:none}
.pillar{position:absolute;top:692px;width:153px;height:262px;background:var(--panel);border-radius:12px;text-align:center}
.pillar-head{height:89px;border-radius:12px 12px 0 0;color:#fff;font-size:16px;font-weight:700;padding-top:13px}
.pillar-head.navy{background:var(--navy)}
.pillar-head.green{background:var(--green)}
.pillar-head .icon-ring{margin:0 auto 8px;width:44px;height:44px;background:transparent;border-color:#fff}
.pillar-head .icon-ring svg{stroke:#fff}
.pillar-body{padding-top:14px;font-size:11.5px;font-weight:700;line-height:17px}
.pillar-body p{margin-bottom:9px}
.plinth{position:absolute;top:957px;width:103px;height:37px;background:#d9dadb;color:var(--red);font-size:15px;font-weight:700;display:flex;align-items:center;justify-content:center}
.base-cap{position:absolute;top:994px;width:127px;height:12px;background:var(--slate)}
.foundation{position:absolute;left:89px;top:1015px;width:634px;height:74px;background:var(--slate);border-radius:12px;color:#fff;font-size:12.5px;font-weight:700}
.foundation .col{position:absolute;top:12px;text-align:center;white-space:nowrap}
.foundation .col span{display:block;line-height:18px;padding:2px 0}
.foundation .col span:first-child{border-bottom:1.5px solid #fff;padding-bottom:6px;margin-bottom:5px}
</style>
</head>
<body>
<div class="sheet">

<!-- ================= PAGE ONE ================= -->
<section class="page page-one">
  <div class="brand"><div class="brand-name">KESTRELWAY</div><div class="brand-sub">FINANCIAL PLANS</div></div>
  <div class="pattern" role="img" aria-label="Decorative triangle pattern in green and grey"></div>

  <h2 class="heading" style="left:53px;top:98px">THE FINANCIAL<span class="accent">CHALLENGE</span></h2>
  <h2 class="heading" style="left:339px;top:98px">FACING<span class="accent">THE CHALLENGE</span></h2>

  <article class="fact-card" style="top:169px;height:285px">
    <div class="fact-photo" role="img" aria-label="Photo backdrop of a person reviewing household finances"></div>
    <div class="fact-title"><span class="icon-ring"><svg viewBox="0 0 24 24"><ellipse cx="11" cy="13" rx="7" ry="5"/><path d="M16 9l3-2v4M6 17v3M14 17v3"/></svg></span>SAVINGS</div>
    <p><b>49%</b> of canadian employees are living paycheque to paycheque. <b>25%</b> of canadians are unable to cover an unexpected <b>$500</b> expense</p>
    <span class="source">Nordata Survey (feb 2023)</span>
    <p><b>25%</b> of canadians need to access their retirement savings early. <b>20%</b> of canadians have no savings. 39% of canadians aged 55-65 have less than <b>$5,000</b> in savings.</p>
    <span class="source">Federal Savings Review (june 2023)</span>
  </article>

  <article class="fact-card" style="top:467px;height:288px">
    <div class="fact-photo" role="img" aria-label="Photo backdrop of banknotes and bills"></div>
    <div class="fact-title"><span class="icon-ring"><svg viewBox="0 0 24 24"><circle cx="12" cy="12" r="7"/><path d="M14 9.5c-.5-.8-1.3-1-2-1-1.3 0-2 .7-2 1.6 0 2.2 4 1.2 4 3.6 0 1-.9 1.8-2 1.8-.9 0-1.7-.4-2.1-1.2M12 7v1.5M12 15.5V17"/></svg></span>DEBT</div>
    <p>The average canadian has <b>$22,131</b> in consumer debt. Which excludes mortgages.</p>
    <span class="source">Creditline Bureau (aug 2024)</span>
    <p>Over <b>55%</b> of canadians hold credit card debt and the total canadian household debt has increased to <b>$2.52trillion</b>, including consumer credit, mortgage and non-mortgage loans.</p>
    <span class="source">Maple Bankers Council (aug 2024)</span>
  </article>

  <article class="fact-card" style="top:769px;height:312px">
    <div class="fact-photo" role="img" aria-label="Photo backdrop of an advisor meeting with a client"></div>
    <div class="fact-title"><span class="icon-ring"><svg viewBox="0 0 24 24"><path d="M12 3l7 3v5c0 5-3 8-7 10-4-2-7-5-7-10V6z"/><path d="M9 12l2 2 4-4"/></svg></span>INSURANCE</div>
    <p><b>45%</b> of canadians do not have individual life insurance coverage, but <b>48%</b> say their families would face financial trouble within 6 months of losing someone.</p>
    <span class="source">Lifewise Research (apr 2023)</span>
    <p>2-in-5 canadians (<b>43%</b> women / <b>44%</b> men) will be diagosed with a form of cancer or other critical illness during their lifetime. Every 7 seconds.</p>
    <span class="source">Wellstat Health Data (june 2024)</span>
  </article>

  <!-- step grid -->
  <div class="tiny" style="left:465px;top:158px">$400<br>$600</div>
  <div class="tri-right" style="left:474px;top:185px"></div>

  <div class="step" style="left:337px;top:187px">
    <span class="icon-ring sm"><svg viewBox="0 0 24 24"><rect x="3" y="7" width="18" height="10" rx="1"/><circle cx="12" cy="12" r="2.5"/></svg></span>
    <div class="step-head">CASH<br>FLOW</div>
    <div class="step-line" style="top:81px">ANALYSZE</div>
    <div class="step-line" style="top:137px">FREE UP</div>
  </div>
  <div class="step" style="left:487px;top:187px">
    <span class="icon-ring sm"><svg viewBox="0 0 24 24"><path d="M3 12a9 9 0 0118 0z"/><path d="M12 12v6a2 2 0 01-4 0"/></svg></span>
    <div class="step-head">CASH FLOW<br>PROTECTION</div>
    <div class="step-line" style="top:81px">INCOME<br>PROTECTION</div>
    <div class="tri" style="left:25px;top:108px"></div>
    <div class="tri" style="left:92px;top:108px"></div>
    <div class="step-line small" style="top:134px;left:0;right:auto;width:70px">Life<br>Insurance</div>
    <div class="step-line small" style="top:134px;left:67px;right:auto;width:68px">CI/DI<br>Insurance</div>
  </div>
  <div class="step" style="left:638px;top:187px">
    <span class="icon-ring sm"><svg viewBox="0 0 24 24"><rect x="3" y="6" width="18" height="13" rx="2"/><path d="M3 10h18M15 15h3"/></svg></span>
    <div class="step-head">DEBT<br>MANAGEMENT</div>
    <div class="step-line" style="top:85px">20%</div>
    <div class="tri" style="left:58px;top:102px"></div>
    <div class="step-line" style="top:137px">6%-7%</div>
  </div>

  <div class="step" style="left:337px;top:394px">
    <span class="icon-ring sm"><svg viewBox="0 0 24 24"><rect x="4" y="8" width="16" height="11" rx="1"/><path d="M8 8V5h8v3M12 11v5M9.5 13.5h5"/></svg></span>
    <div class="step-head">EMERGENCY<br>FUND</div>
    <div class="step-line" style="top:81px">IF/ WHEN</div>
    <div class="tri" style="left:58px;top:99px"></div>
    <div class="step-line" style="top:121px">3/6<br>Months</div>
  </div>
  <div class="step" style="left:487px;top:394px">
    <span class="icon-ring sm"><svg viewBox="0 0 24 24"><path d="M4 19h16M6 19v-5M10 19V10M14 19v-7M18 19V6"/></svg></span>
    <div class="step-head">BUILD<br>WEALTH</div>
    <div class="step-line" style="top:81px">FINANCIAL<br>INDEPENDENCE<br>NUMBER<br>(F.I.N)</div>
    <svg class="abs" style="left:56px;top:141px" width="22" height="20" viewBox="0 0 22 20" fill="none" stroke="#0e2235" stroke-width="1.6"><rect x="2" y="6" width="18" height="12" rx="1"/><path d="M2 10h18M7 6V3h8v3"/></svg>
  </div>
  <div class="step" style="left:638px;top:394px">
    <span class="icon-ring sm"><svg viewBox="0 0 24 24"><rect x="4" y="4" width="16" height="16" rx="2"/><circle cx="12" cy="12" r="3.5"/></svg></span>
    <div class="step-head">RESERVE<br>WEALTH</div>
    <div class="step-line" style="top:81px">LEAVING<br>A LEGACY</div>
    <div class="step-line" style="top:138px">Will Prep</div>
  </div>

  <h2 class="heading" style="left:339px;top:584px">HOW<span class="accent">WE WILL DO IT</span></h2>

  <svg class="abs" style="left:456px;top:640px" width="200" height="200" viewBox="0 0 200 200" font-family="Montserrat, sans-serif" font-weight="700">
    <path d="M100 100 L100 5 A95 95 0 0 0 100 195 Z" fill="#0e2235"/>
    <path d="M100 100 L100 5 A95 95 0 0 1 182.3 52.5 Z" fill="#0e2235"/>
    <path d="M100 100 L182.3 52.5 A95 95 0 0 1 191.8 124.6 Z" fill="#b9f3cb"/>
    <path d="M100 100 L191.8 124.6 A95 95 0 0 1 100 195 Z" fill="#16b14a"/>
    <line x1="100" y1="5" x2="100" y2="195" stroke="#fff" stroke-width="2"/>
    <line x1="100" y1="100" x2="182.3" y2="52.5" stroke="#fff" stroke-width="2"/>
    <line x1="100" y1="100" x2="191.8" y2="124.6" stroke="#fff" stroke-width="2"/>
    <text x="110" y="62" fill="#fff" font-size="12.5">Taxes</text>
    <text x="128" y="102" fill="#0e2235" font-size="12.5">SAVINGS</text>
    <text x="110" y="173" fill="#fff" font-size="12.5">Debt</text>
    <text x="55" y="124" fill="#fff" font-size="12.5" text-anchor="middle">Living</text>
    <text x="55" y="141" fill="#fff" font-size="12.5" text-anchor="middle">Expenses</text>
  </svg>

  <div class="tri grey" style="left:548px;top:843px"></div>

  <div class="service" style="left:341px"><span class="icon-ring"><svg viewBox="0 0 24 24"><path d="M4 20h16M6 20v-6h12v6M9 14V9h6v5"/></svg></span>RETIREMENT<br>SAVINGS</div>
  <div class="service" style="left:452px"><span class="icon-ring"><svg viewBox="0 0 24 24"><path d="M2 9l10-4 10 4-10 4z"/><path d="M6 11v5c3 2 9 2 12 0v-5"/></svg></span>CHILDRREN'S<br>EDUCATION</div>
  <div class="service" style="left:562px"><span class="icon-ring"><svg viewBox="0 0 24 24"><path d="M12 3l7 3v5c0 5-3 8-7 10-4-2-7-5-7-10V6z"/></svg></span>PROPER<br>PROTECTION</div>
  <div class="service" style="left:672px"><span class="icon-ring"><svg viewBox="0 0 24 24"><path d="M5 12l4 4 10-10"/></svg></span>FREEDOM<br>FROM DEBT</div>

  <div class="tri grey" style="left:548px;top:957px"></div>

  <div class="partner" style="left:341px;top:977px">Harbourline</div>
  <div class="partner" style="left:452px;top:977px">Northlake Life</div>
  <div class="partner" style="left:562px;top:977px">Daybreak Life</div>
  <div class="partner" style="left:672px;top:977px">Cedarmount</div>
  <div class="partner" style="left:341px;top:1022px">Amberly Group</div>
  <div class="partner" style="left:452px;top:1022px">Royalton<br>Insurance</div>
  <div class="partner" style="left:562px;top:1022px">Verida</div>
  <div class="partner" style="left:672px;top:1022px">Bayfield<br>Insurance</div>
  <div class="partner" style="left:396px;top:1068px">Clearpath Advisor</div>
  <div class="partner" style="left:506px;top:1068px">Fairmont Life</div>
  <div class="partner" style="left:616px;top:1068px">Ostara</div>

  <footer class="footer" style="top:1143px">©KESTRELWAY | FINANCIAL PLANS <span class="num">1</span></footer>
</section>

<!-- ================= PAGE TWO ================= -->
<section class="page page-two">
  <div class="upper"></div>
  <div class="brand"><div class="brand-name">KESTRELWAY</div><div class="brand-sub">FINANCIAL PLANS</div></div>
  <div class="pattern" role="img" aria-label="Decorative triangle pattern in green and grey"></div>

  <h2 class="heading" style="left:53px;top:108px">RULE OF 72</h2>

  <div class="rate-block first" style="left:53px;width:174px">
    <div class="rate-head"><span class="age" style="width:89px">AGE</span><span class="pct">4%</span></div>
    <div class="rate-row"><span class="a" style="width:89px">29</span><span>$10,000</span></div>
    <div class="rate-row"><span class="a" style="width:89px">47</span><span>$20,000</span></div>
    <div class="rate-row"><span class="a" style="width:89px">65</span><span>$40,000</span></div>
  </div>
  <div class="rate-block" style="left:227px;width:178px">
    <div class="rate-head" style="margin-left:8px"><span class="age" style="width:85px">AGE</span><span class="pct">6%</span></div>
    <div class="rate-row"><span class="a" style="width:93px">29</span><span>$10,000</span></div>
    <div class="rate-row"><span class="a" style="width:93px">41</span><span>$20,000</span></div>
    <div class="rate-row"><span class="a" style="width:93px">53</span><span>$40,000</span></div>
    <div class="rate-row"><span class="a" style="width:93px">65</span><span>$80,000</span></div>
  </div>
  <div class="rate-block" style="left:405px;width:177px">
    <div class="rate-head" style="margin-left:8px"><span class="age" style="width:85px">AGE</span><span class="pct">8%</span></div>
    <div class="rate-row"><span class="a" style="width:93px">29</span><span>$10,000</span></div>
    <div class="rate-row"><span class="a" style="width:93px">38</span><span>$20,000</span></div>
    <div class="rate-row"><span class="a" style="width:93px">47</span><span>$40,000</span></div>
    <div class="rate-row"><span class="a" style="width:93px">56</span><span>$80,000</span></div>
    <div class="rate-row"><span class="a" style="width:93px">65</span><span>$160,000</span></div>
  </div>
  <div class="rate-block" style="left:582px;width:182px">
    <div class="rate-head" style="margin-left:9px"><span class="age" style="width:85px">AGE</span><span class="pct">12%</span></div>
    <div class="rate-row"><span class="a" style="width:94px">29</span><span>$10,000</span></div>
    <div class="rate-row"><span class="a" style="width:94px">35</span><span>$20,000</span></div>
    <div class="rate-row"><span class="a" style="width:94px">41</span><span>$40,000</span></div>
    <div class="rate-row"><span class="a" style="width:94px">47</span><span>$80,000</span></div>
    <div class="rate-row"><span class="a" style="width:94px">53</span><span>$160,000</span></div>
    <div class="rate-row"><span class="a" style="width:94px">59</span><span>$320,000</span></div>
  </div>

  <div class="doubles" style="left:70px">
    <svg viewBox="0 0 50 40" fill="none" stroke="#0e2235" stroke-width="1.6"><rect x="2" y="8" width="32" height="16" rx="2"/><rect x="5" y="14" width="32" height="16" rx="2" fill="#f1f1f1"/><circle cx="21" cy="22" r="4"/><circle cx="39" cy="28" r="8" fill="#f1f1f1" stroke="#16b14a"/><path d="M39 24v8" stroke="#16b14a"/></svg>
    <span class="doubles-text"><span class="lead">MONEY<br>DOUBLES</span><span class="every">EVERY<br>18 YEARS</span></span>
  </div>
  <div class="doubles" style="left:252px">
    <svg viewBox="0 0 50 40" fill="none" stroke="#0e2235" stroke-width="1.6"><rect x="2" y="8" width="32" height="16" rx="2"/><rect x="5" y="14" width="32" height="16" rx="2" fill="#f1f1f1"/><circle cx="21" cy="22" r="4"/><circle cx="39" cy="28" r="8" fill="#f1f1f1" stroke="#16b14a"/><path d="M39 24v8" stroke="#16b14a"/></svg>
    <span class="doubles-text"><span class="lead">MONEY<br>DOUBLES</span><span class="every">EVERY<br>12 YEARS</span></span>
  </div>
  <div class="doubles" style="left:432px">
    <svg viewBox="0 0 50 40" fill="none" stroke="#0e2235" stroke-width="1.6"><rect x="2" y="8" width="32" height="16" rx="2"/><rect x="5" y="14" width="32" height="16" rx="2" fill="#f1f1f1"/><circle cx="21" cy="22" r="4"/><circle cx="39" cy="28" r="8" fill="#f1f1f1" stroke="#16b14a"/><path d="M39 24v8" stroke="#16b14a"/></svg>
    <span class="doubles-text"><span class="lead">MONEY<br>DOUBLES</span><span class="every">EVERY<br>9 YEARS</span></span>
  </div>
  <div class="doubles" style="left:610px">
    <svg viewBox="0 0 50 40" fill="none" stroke="#0e2235" stroke-width="1.6"><rect x="2" y="8" width="32" height="16" rx="2"/><rect x="5" y="14" width="32" height="16" rx="2" fill="#f1f1f1"/><circle cx="21" cy="22" r="4"/><circle cx="39" cy="28" r="8" fill="#f1f1f1" stroke="#16b14a"/><path d="M39 24v8" stroke="#16b14a"/></svg>
    <span class="doubles-text"><span class="lead">MONEY<br>DOUBLES</span><span class="every">EVERY<br>6 YEARS</span></span>
  </div>

  <h2 class="heading" style="left:53px;top:522px">STRUCTURE</h2>
  <div class="no-sign"><span>FundTogether</span><span class="ring"></span></div>

  <svg class="abs" style="left:53px;top:565px" width="712" height="112" viewBox="0 0 712 112">
    <polygon points="62,53 324,0 390,0 652,53" fill="#b7bbc0"/>
    <rect x="0" y="53" width="712" height="10" fill="#cdd0d3"/>
    <rect x="38" y="70" width="634" height="21" fill="#dcdedf"/>
    <rect x="38" y="98" width="127" height="12" fill="#b7bbc0"/>
    <rect x="207" y="98" width="126" height="12" fill="#b7bbc0"/>
    <rect x="376" y="98" width="126" height="12" fill="#b7bbc0"/>
    <rect x="545" y="98" width="127" height="12" fill="#b7bbc0"/>
  </svg>

  <div class="pillar" style="left:78px">
    <div class="pillar-head navy"><span class="icon-ring"><svg viewBox="0 0 24 24"><path d="M4 11l8-7 8 7M6 10v10h12V10M10 20v-5h4v5"/></svg></span>HOME</div>
    <div class="pillar-body"><p>PARTNER WITH<br>MORTGAGE<br>BROKERS FOR<br>BEST RATES</p><p>MORTGAGE<br>INSURANCE<br>ALTERNATIVES</p></div>
  </div>
  <div class="pillar" style="left:247px">
    <div class="pillar-head green"><span class="icon-ring"><svg viewBox="0 0 24 24"><ellipse cx="11" cy="13" rx="7" ry="5"/><path d="M16 9l3-2v4M6 17v3M14 17v3"/></svg></span>RRSP</div>
    <div class="pillar-body"><p>TAX DEDUCTION</p><p>TAX DEFERRED</p></div>
  </div>
  <div class="pillar" style="left:415px">
    <div class="pillar-head navy"><span class="icon-ring"><svg viewBox="0 0 24 24"><path d="M3 9l9-5 9 5M5 9v9M10 9v9M14 9v9M19 9v9M3 20h18"/></svg></span>TFSA</div>
    <div class="pillar-body"><p>NO TAX<br>DEDUCTIONS</p><p>TAX FREE<br>GROWTH</p><p>2009-$102,000</p><p>2025 LIMIT -<br>$7000/YR</p></div>
  </div>
  <div class="pillar" style="left:585px">
    <div class="pillar-head green"><span class="icon-ring"><svg viewBox="0 0 24 24"><circle cx="8" cy="9" r="2.5"/><circle cx="16" cy="9" r="2.5"/><path d="M4 18c0-3 2-5 4-5s4 2 4 5M12 18c0-3 2-5 4-5s4 2 4 5"/></svg></span>PERM LIFE</div>
    <div class="pillar-body"><p>NO TAX<br>DEDUCTION</p><p>QUALIFY</p><p>TAX DEFERRED<br>GROWTH</p></div>
  </div>

  <div class="plinth" style="left:103px">SELL</div>
  <div class="plinth" style="left:272px">100% TAX</div>
  <div class="plinth" style="left:440px">0% TAX</div>
  <div class="plinth" style="left:610px">0% TAX</div>
  <div class="base-cap" style="left:91px"></div>
  <div class="base-cap" style="left:260px"></div>
  <div class="base-cap" style="left:429px"></div>
  <div class="base-cap" style="left:598px"></div>

  <div class="foundation">
    <div class="col" style="left:56px;width:280px"><span>EMERGENCY/OPPORTUNITY FUNDS</span><span>CASHFLOW PROTECTION (LI/CI/DI)</span></div>
    <div class="col" style="left:356px;width:230px"><span>DEBT MANAGEMENT</span><span>CASH FLOW</span></div>
  </div>

  <footer class="footer" style="top:1141px">©KESTRELWAY | FINANCIAL PLANS <span class="num">2</span></footer>
</section>

</div>
</body>
</html>
```